Los Brava Dip – CPG Website with WordPress - Store Locator: WP Maps plugin

Larkfield Food Company is a startup consumer packaged goods (CPG) brand launching its flagship product line — Los Brava Dip. We’re seeking a talented web designer to create a bold, professional, mobile-optimized website using WordPress with a WP Maps store locator to help customers find local retailers.

Our goal is to build a strong online presence that supports both retail growth and direct-to-consumer sales.

See Los Brava _Website_Design_Brief word document.

The website URL is https://losbravadip.example/

Target Market(s)

Consumers of gourmet salsa

Industry/Entity Type

Consumer Packaged Goods - Salsa manufacturer.

Coding

Coded - Design and coding required

Number of Pages Required

5+ page

Requirements
Must have
• The design of the Los Brava Dip website shall emulate the clean, polished aesthetic of Fennigo.example.

```html
<!DOCTYPE html>
<html lang="en">
<head>
<meta charset="utf-8">
<title>Privacy Policy – Los Brava Dip</title>
<link rel="stylesheet" href="https://fonts.googleapis.com/css2?family=Outfit:wght@400;500;600;700&family=Oswald:wght@600&display=swap">
<style>
  :root {
    --brand-red: #c8202a;
    --ink: #1b1b1b;
    --muted: #444;
    --rule: #d6d6d6;
    --white: #ffffff;
    --hero-gold: #f4a623;
    --hero-orange: #e35a0e;
    --hero-deep: #5c140c;
  }
  * { box-sizing: border-box; margin: 0; padding: 0; }
  html, body { width: 706px; height: 1200px; overflow: hidden; background: var(--white); }
  body { font-family: "Outfit", sans-serif; color: var(--ink); position: relative; }

  .site-header {
    position: absolute; top: 0; left: 0; width: 706px; height: 47px;
    background: var(--white); z-index: 2;
  }
  .brand-tab {
    position: absolute; left: 58px; top: 0; width: 96px; height: 62px;
    background: var(--white); border-radius: 0 0 48px 48px / 0 0 18px 18px;
    display: flex; align-items: center; justify-content: center; padding-bottom: 14px;
  }
  .brand-name { font-weight: 700; color: var(--brand-red); font-size: 18px; letter-spacing: -0.2px; }
  .main-nav {
    position: absolute; left: 192px; top: 0; height: 47px;
    display: flex; align-items: center; gap: 0;
  }
  .main-nav a {
    font-size: 8px; font-weight: 600; letter-spacing: 1.1px; color: var(--ink);
    text-decoration: none; text-transform: uppercase; margin-right: 31px;
  }
  .contact-btn {
    position: absolute; left: 563px; top: 15px; width: 76px; height: 20px;
    background: var(--brand-red); color: var(--white); border-radius: 10px;
    font-size: 8px; font-weight: 600; letter-spacing: 1.1px;
    display: flex; align-items: center; justify-content: center; text-decoration: none;
  }

  .hero {
    position: absolute; top: 47px; left: 0; width: 706px; height: 190px; overflow: hidden;
  }
  .hero-art {
    position: absolute; inset: 0;
    background: linear-gradient(100deg, var(--hero-gold) 0%, #ec8a18 28%, var(--hero-orange) 48%, #9a2310 70%, var(--hero-deep) 100%);
  }
  .hero-title {
    position: absolute; left: 0; right: 0; top: 62px; text-align: center;
    font-family: "Oswald", sans-serif; font-weight: 600; font-size: 36px;
    letter-spacing: 1px; color: var(--white);
  }
  .hero-underline { position: absolute; left: 293px; top: 108px; }

  .policy {
    position: absolute; top: 277px; left: 60px; width: 585px;
    font-size: 13px; line-height: 16.8px;
  }
  .policy p, .policy ul { margin-bottom: 16.6px; }
  .policy .effective { font-weight: 700; margin-bottom: 17px; }
  .policy h2 { font-size: 13px; line-height: 16.8px; font-weight: 700; }
  .policy h2.plain { font-weight: 400; }
  .policy ul.list { list-style: none; margin-bottom: 0; }
  .policy ul.list li { position: relative; padding-left: 16px; }
  .policy ul.list li::before { content: "•"; position: absolute; left: 0; font-size: 9px; }
  .policy .tight { margin-bottom: 0; }

  .site-footer {
    position: absolute; top: 1077px; left: 0; width: 706px; height: 123px;
    border-top: 1px solid var(--rule);
  }
  .footer-brand {
    position: absolute; left: 0; top: 0; width: 166px; height: 123px;
    border-right: 1px solid var(--rule);
    display: flex; align-items: center; justify-content: center; padding-bottom: 14px;
  }
  .footer-brand .brand-name { font-size: 22px; }
  .footer-nav {
    position: absolute; left: 198px; top: 36px; display: flex; align-items: center;
  }
  .footer-nav a {
    font-size: 8px; font-weight: 500; letter-spacing: 1px; color: var(--ink); text-decoration: none;
  }
  .footer-nav .sep { width: 3px; height: 3px; background: var(--brand-red); margin: 0 15px; }
  .footer-rule { position: absolute; left: 166px; right: 18px; top: 69px; border-top: 1px solid var(--rule); }
  .footer-meta {
    position: absolute; left: 195px; top: 85px; width: 420px; height: 18px;
    font-size: 7px; color: var(--muted); display: flex; align-items: center;
  }
  .social { position: absolute; left: 262px; display: flex; gap: 4px; }
  .social span { width: 17px; height: 17px; border-radius: 50%; background: var(--ink); display: block; }
  .legal { position: absolute; left: 314px; display: flex; gap: 9px; font-size: 7.5px; }
  .legal a { color: var(--muted); text-decoration: none; }
</style>
</head>
<body>
  <header class="site-header">
    <div class="brand-tab"><span class="brand-name">Los Brava</span></div>
    <nav class="main-nav">
      <a href="#">About</a>
      <a href="#">Products</a>
      <a href="#">Where to Buy</a>
      <a href="#">Recipes</a>
      <a href="#">Reviews</a>
    </nav>
    <a class="contact-btn" href="#">CONTACT ›</a>
  </header>

  <section class="hero">
    <div class="hero-art" role="img" aria-label="Bold abstract flame shapes in gold, orange, deep red and dark green"></div>
    <h1 class="hero-title">PRIVACY POLICY</h1>
    <svg class="hero-underline" width="155" height="8" viewBox="0 0 155 8" aria-hidden="true">
      <path d="M2 6 C40 1, 110 0, 153 3" stroke="#fff" stroke-width="3" fill="none" stroke-linecap="round"/>
    </svg>
  </section>

  <main class="policy">
    <p class="effective">Effective Date: June 2025</p>
    <p>At Los Brava Dip, we respect your privacy and are committed to transparency about how we collect and use data on our website, www.losbravadip.example.</p>

    <h2 class="plain">1. Information We Collect</h2>
    <p>We do not collect any personal information such as names, emails, or payment details.<br>The only data we collect is through cookies, which track general website usage.</p>

    <h2>2. How We Collect Data</h2>
    <p class="tight">We use cookies to collect anonymous usage data when you visit our site. This data may include:</p>
    <ul class="list">
      <li>Browser type</li><li>Device type</li><li>Pages visited</li><li>Time spent on the site</li><li>Referral sources</li>
    </ul>
    <p>This data is collected via tools like Trackwise Analytics.</p>

    <h2>3. How We Use Your Information</h2>
    <p class="tight">We use this anonymous usage data strictly to:</p>
    <ul class="list">
      <li>Improve our website’s performance</li><li>Understand how users interact with our content</li><li>Enhance the overall user experience</li>
    </ul>
    <p>We do not sell, share, or disclose this data to any third parties.</p>

    <h2>4. Cookies and Tracking</h2>
    <p>We use cookies to better understand visitor behavior. You can disable cookies through your browser settings if you prefer not to be tracked.</p>

    <h2>5. Your Rights</h2>
    <p>While we do not collect personally identifiable information, you may contact us at any time to inquire about or request the removal of usage data associated with your visit: [support@losbravadip.example]</p>

    <h2>6. Data Security</h2>
    <p>We protect all collected data using industry-standard security measures, including SSL encryption.</p>

    <h2>7. Policy Updates</h2>
    <p>This Privacy Policy may be updated from time to time. Any changes will be posted on this page with an updated effective date.</p>

    <h2>8. Contact Us</h2>
    <p>If you have any questions or concerns about this policy, please contact us at:<br>support@losbravadip.example</p>
  </main>

  <footer class="site-footer">
    <div class="footer-brand"><span class="brand-name">Los Brava</span></div>
    <nav class="footer-nav">
      <a href="#">ABOUT</a><span class="sep"></span>
      <a href="#">PRODUCTS</a><span class="sep"></span>
      <a href="#">WHERE TO BUY</a><span class="sep"></span>
      <a href="#">RECIPES</a><span class="sep"></span>
      <a href="#">REVIEWS</a><span class="sep"></span>
      <a href="#">CONTACT</a>
    </nav>
    <div class="footer-rule"></div>
    <div class="footer-meta">
      <span>© 2025 Larkfield Food Company. All rights reserved.</span>
      <div class="social" aria-label="Social links"><span></span><span></span></div>
      <div class="legal"><a href="#">Privacy Policy</a><a href="#">Terms of Use</a></div>
    </div>
  </footer>
</body>
</html>
```